A modern, fresh introduction to Buddhism

I need a book cover for an A6 sized book to be used both for ebook and hard copy. The author is a young, modern Buddhist teacher of high standing who has written this short intro to Buddhism in an informal Q & As format using modern, accessible language to convey profound and meaningful ideas to the general public. The author is Tibetan, but teaches worldwide and is very personable and dynamic. The cover should portray this and have a fresh yet authentic feel to it (nothing new-agey!). Please see the author's websites www.torvenmalsiteacher.org and www.vrmq.org for reference, but do not feel that the design must align completely with the website designs.

Target Market(s)

General public both in Europe and America and in Asia ranging from teenagers to the elderly. A really broad audience.

Industry/Entity Type

Teacher

Requirements
Must have
• Please include the following text that on the front cover:

A Window Onto Stillwaters

By Dorwel Tamsung Geshela

Please include the following on the back cover:

Mirun Teskavo Publications (with attached logo above it)
Nice to have
• A simplistic, artistic, and modern look without any traditional religious images.
Should not have
• No buddha images or religious images. I would prefer a more simplistic, modern and artistic look.

```html
<!DOCTYPE html>
<html lang="en">
<head>
<meta charset="utf-8">
<title>A Window Onto Stillwaters — Book Cover</title>
<link rel="stylesheet" href="https://fonts.googleapis.com/css2?family=Anton&family=Roboto+Condensed:wght@400&display=swap">
<style>
  :root {
    --mist-light: #eef0ee;
    --mist-mid: #d3d7d4;
    --mist-deep: #aab0ab;
    --tree-shadow: #5f665e;
    --foliage-dark: #33402a;
    --foliage-mid: #5e6d48;
    --cloth-red: #a8283a;
    --cloth-teal: #4fa3a0;
    --cloth-gold: #d9a640;
    --band-yellow: #f3bd1a;
    --cover-orange: #f4a11f;
    --ink-grey: #474545;
  }
  html, body {
    margin: 0;
    padding: 0;
    overflow: hidden;
    background: #ffffff;
  }
  .cover {
    position: relative;
    width: 848px;
    height: 1200px;
    overflow: hidden;
    background: var(--cover-orange);
  }
  .cover-photo {
    position: absolute;
    left: 0;
    top: 0;
    width: 848px;
    height: 728px;
    background:
      radial-gradient(ellipse 260px 120px at 330px 560px, rgba(217,166,64,0.45), transparent 70%),
      radial-gradient(ellipse 220px 110px at 170px 520px, rgba(79,163,160,0.40), transparent 70%),
      radial-gradient(ellipse 160px 90px at 40px 340px, rgba(168,40,58,0.45), transparent 70%),
      radial-gradient(ellipse 180px 120px at 560px 600px, rgba(168,40,58,0.25), transparent 70%),
      radial-gradient(ellipse 320px 300px at 470px 300px, rgba(95,102,94,0.55), transparent 72%),
      radial-gradient(ellipse 260px 160px at 760px 560px, rgba(51,64,42,0.75), transparent 75%),
      radial-gradient(ellipse 200px 160px at 60px 560px, rgba(51,64,42,0.55), transparent 75%),
      linear-gradient(180deg,
        var(--mist-light) 0%,
        var(--mist-mid) 40%,
        var(--mist-deep) 62%,
        var(--foliage-mid) 82%,
        var(--foliage-dark) 100%);
  }
  .author-band {
    position: absolute;
    left: 0;
    top: 728px;
    width: 848px;
    height: 78px;
    background: var(--band-yellow);
    display: flex;
    align-items: center;
    justify-content: center;
  }
  .author-name {
    margin: 0;
    font-family: "Roboto Condensed", "Arial Narrow", sans-serif;
    font-weight: 400;
    font-size: 29px;
    color: var(--ink-grey);
  }
  .title-block {
    position: absolute;
    left: 0;
    top: 910px;
    width: 848px;
    text-align: center;
  }
  .book-title {
    margin: 0;
    font-family: "Anton", "Impact", sans-serif;
    font-weight: 400;
    font-size: 70px;
    line-height: 1.05;
    color: var(--ink-grey);
    letter-spacing: 0.3px;
  }
  .book-subtitle {
    margin: 8px 0 0;
    font-family: "Roboto Condensed", "Arial Narrow", sans-serif;
    font-weight: 400;
    font-size: 40px;
    line-height: 1.2;
    color: var(--ink-grey);
  }
</style>
</head>
<body>
  <main class="cover">
    <div class="cover-photo" role="img" aria-label="Photograph of a string of colourful cloth flags stretched across a misty forest clearing with tall trees in fog"></div>
    <div class="author-band">
      <p class="author-name">Dorwel Tamsung Geshela</p>
    </div>
    <div class="title-block">
      <h1 class="book-title">A Window Onto Stillwaters</h1>
      <p class="book-subtitle">A Short Introduction to the Buddha's Teaching</p>
    </div>
  </main>
</body>
</html>
```